Architectural, Engineering and Design Build

Tovandex4.com
Veteran Disabled Certified company is doing business in Architecture, Engineer and Design build - look simialr websites and come up with design follow following website
https://hollis-darnet.example/
https://www.venlorcogroup.example/
https://www.pembrisgc.example/contract-vehicles/service-disabled-veteran-owned-small-business-sdvosb/
https://www.corbelnetlink.example/about/sdvosb/

Target Market(s)

US - Defense and Federal Government

Industry/Entity Type

Colors
0054AA
0677BA
7BADD7
CADEEF
E8F1F8

Requirements
Must have
• Army, American patriotism , Buildings, construction, architecture, engineering
Nice to have
• I need to attract federal government agencies and Defense

```html
<!DOCTYPE html>
<html lang="en">
<head>
<meta charset="utf-8">
<title>Tovandex4 — Architecture, Engineering &amp; Design Build</title>
<link rel="stylesheet" href="https://fonts.googleapis.com/css2?family=Exo+2:wght@500;600;700&family=Poppins:wght@400;500;600&display=swap">
<style>
:root{
  --navy:#14225f;
  --red:#d7141f;
  --ink:#1a1a1a;
  --muted:#4a4a4a;
  --grey-bg:#f0f0f0;
  --white:#ffffff;
  --footer-bg:#f2f2f2;
}
*{box-sizing:border-box;margin:0;padding:0}
html,body{width:1200px;height:4847px;overflow:hidden}
body{font-family:"Poppins",sans-serif;color:var(--ink);background:var(--white);position:relative}
.section{position:absolute;left:0;width:1200px}
.abs{position:absolute}
.heading{font-family:"Exo 2",sans-serif;font-weight:700;font-size:31px;color:var(--ink);text-transform:uppercase;letter-spacing:.2px;white-space:nowrap}
.heading-center{text-align:center;width:100%}
.rule{display:block;width:44px;height:4px;background:var(--red);margin:8px auto 0}
.rule-left{margin:8px 0 0}
.btn{display:inline-flex;align-items:center;justify-content:center;background:var(--navy);color:#fff;font-size:11.5px;border-radius:24px;height:42px;padding:0 34px;font-family:"Poppins",sans-serif}
.body-text{font-size:11.5px;line-height:23px;color:var(--muted)}
.photo{border-radius:22px}

/* hero */
.hero{top:0;height:600px;background:linear-gradient(180deg,#6b7683 0%,#8b8f94 35%,#9c9a95 60%,#7b7870 100%)}
.hero-shade{position:absolute;inset:0;background:rgba(20,25,35,.35)}
.brand{position:absolute;left:141px;top:40px;display:flex;align-items:center;gap:10px;font-family:"Exo 2",sans-serif;font-weight:700;font-size:24px;color:#fff}
.brand-dot{width:18px;height:18px;border-radius:50%;background:#fff}
.nav{position:absolute;top:54px;right:141px;display:flex;gap:46px;font-size:11px;color:#fff}
.nav .active{color:var(--red)}
.hero-title{position:absolute;top:272px;width:100%;text-align:center;font-family:"Exo 2",sans-serif;font-weight:700;font-size:42px;color:#fff}
.hero-btn{position:absolute;top:348px;left:521px;height:38px;padding:0 30px;background:var(--red);color:#fff;font-size:11px;border-radius:22px;display:flex;align-items:center}

/* about */
.about{top:600px;height:570px}
.about-text{left:647px;top:132px;width:420px}
.about-text p{margin-top:22px}
.about-text strong{color:var(--ink);font-weight:600}

/* services */
.services{top:1170px;height:619px;background:var(--grey-bg)}
.service-card{position:absolute;top:150px;width:290px;height:367px;background:#fff;border-radius:18px;text-align:center}
.service-card .photo{margin:16px auto 0;width:258px;height:242px;border-radius:16px}
.service-card h3{font-size:15px;font-weight:600;margin-top:18px}
.service-card p{font-size:11.5px;line-height:20px;color:var(--muted);padding:4px 30px 0}
.circle-btn{width:32px;height:32px;border-radius:50%;background:var(--navy);display:flex;align-items:center;justify-content:center;margin:8px auto 0}

/* certifications */
.certs{top:1789px;height:325px}
.cert-badge{position:absolute;top:120px;width:130px;height:82px;background:#fff;border-radius:6px;box-shadow:0 2px 12px rgba(0,0,0,.12);display:flex;align-items:center;justify-content:center}
.cert-badge span{display:block;width:76px;height:36px;border-radius:6px}

/* gallery */
.gallery{top:2114px;height:696px;background:var(--grey-bg)}
.project{position:absolute;top:186px;width:442px}
.project .photo{height:247px;border-radius:18px}
.project h3{font-size:15px;font-weight:600;line-height:23px;margin-top:12px}
.project p{margin-top:12px}

/* why */
.why{top:2810px;height:502px}
.why-card{position:absolute;top:228px;width:284px;height:188px;background:#fff;border-radius:14px;box-shadow:0 3px 14px rgba(0,0,0,.1);text-align:center}
.why-card h3{font-size:14px;font-weight:600;line-height:20px;margin-top:82px}
.why-card p{font-size:11px;line-height:19px;color:var(--muted);margin-top:12px;padding:0 34px}
.why-icon{position:absolute;top:182px;width:108px;height:108px}

/* testimonials */
.reviews{top:3312px;height:563px;background:var(--grey-bg)}
.review-card{position:absolute;top:168px;width:275px;height:244px;background:#fff;border-radius:12px;padding:22px 22px 0}
.review-card p{font-size:11.5px;line-height:23px;color:var(--muted);margin-top:6px}
.stars{color:#f5b400;font-size:14px;letter-spacing:4px}
.reviewer{display:flex;align-items:center;gap:12px;margin-top:16px;font-size:14px}
.avatar{width:56px;height:56px;border-radius:50%;background:linear-gradient(135deg,#6f7a5a,#3f4a36)}
.quote{position:absolute;top:-14px;right:-4px;width:42px;height:42px;border-radius:50%;background:var(--red)}

/* cta */
.cta{top:3875px;height:570px}
.cta h2{font-family:"Exo 2",sans-serif;font-weight:700;font-size:31px;line-height:42px}
.cta p{font-size:13px;line-height:24px;color:var(--muted);margin-top:24px}

/* footer */
.footer{top:4445px;height:350px;background:var(--footer-bg)}
.footer h4{font-size:15px;font-weight:600}
.footer .rule{margin:8px 0 0;width:28px;height:3px}
.footer ul{list-style:none;margin-top:18px}
.footer li{font-size:11px;margin-bottom:15px;display:flex;align-items:center;gap:8px}
.contact-item{display:flex;gap:10px;margin-top:16px;font-size:11px;line-height:19px}
.contact-item b{font-weight:600}
.social-ring{width:28px;height:28px;border-radius:50%;border:1.5px solid var(--ink)}
.copyright{top:4795px;height:52px;background:var(--red);color:#fff;font-size:11px;display:flex;align-items:center;justify-content:center}
</style>
</head>
<body>

<header class="section hero">
  <div class="hero-shade" role="img" aria-label="Photo of a domed government capitol building under cloudy sky"></div>
  <div class="brand"><span class="brand-dot"></span>TOVANDEX4</div>
  <nav class="nav"><span class="active">Home</span><span>About Us</span><span>Services</span><span>Projects</span><span>Contact Us</span></nav>
  <h1 class="hero-title">BUILDING FOR THE FUTURE OF DEFENSE</h1>
  <a class="hero-btn">Contact Us Today!</a>
</header>

<section class="section about">
  <div class="abs photo" style="left:141px;top:85px;width:401px;height:398px;background:linear-gradient(180deg,#7aa7c8 0%,#d9b890 55%,#1c1c1c 80%)" role="img" aria-label="Construction workers silhouetted on scaffolding at sunset"></div>
  <div class="abs about-text">
    <h2 class="heading" style="font-size:29px">About Tovandex4</h2>
    <span class="rule rule-left"></span>
    <p class="body-text">Lorem ipsum dolor sit amet, consectetur adipiscing elit, sed do eiusmod ut tempor incididunt ut labore et dolore magna aliqua. Ut enim ad minim ex veniam, quis nostrud exercitation ullamco laboris nisi ut aliquip ex ea amet commodo consequat. Duis aute irure dolor in reprehenderit in voluptate velit esse cillum dolore eu fugiat nulla pariatur.</p>
    <p class="body-text" style="margin-top:4px"><strong>Our Mission</strong> : Sed ut perspiciatis unde omnis iste natus error sit amet ex ea voluptatem accusantium doloremque laudantium.</p>
    <a class="btn" style="margin-top:18px;height:40px">Read More</a>
  </div>
</section>

<section class="section services">
  <div class="abs" style="top:80px;width:100%"><h2 class="heading heading-center">Our Services</h2><span class="rule"></span></div>
  <article class="service-card" style="left:141px">
    <div class="photo" style="background:linear-gradient(160deg,#e8e2da,#c9bfae)" role="img" aria-label="Architect sketching plans beside a hard hat and magnifier"></div>
    <h3>Architectural</h3>
    <p>Lorem ipsum dolor sit amet, consectetur adipiscing elit.</p>
    <div class="circle-btn"><svg width="12" height="12" viewBox="0 0 12 12"><path d="M4 2l4 4-4 4" stroke="#fff" stroke-width="2" fill="none"/></svg></div>
  </article>
  <article class="service-card" style="left:455px">
    <div class="photo" style="background:linear-gradient(160deg,#b8c3cc,#8a8f7a)" role="img" aria-label="Engineer in safety vest reviewing blueprints on site"></div>
    <h3>Engineering Work</h3>
    <p>Lorem ipsum dolor sit amet, consectetur adipiscing elit.</p>
    <div class="circle-btn"><svg width="12" height="12" viewBox="0 0 12 12"><path d="M4 2l4 4-4 4" stroke="#fff" stroke-width="2" fill="none"/></svg></div>
  </article>
  <article class="service-card" style="left:769px">
    <div class="photo" style="background:linear-gradient(160deg,#e6e3dd,#9c9a8c)" role="img" aria-label="Designers drafting building plans at a table"></div>
    <h3>Design Build</h3>
    <p>Lorem ipsum dolor sit amet, consectetur adipiscing elit.</p>
    <div class="circle-btn"><svg width="12" height="12" viewBox="0 0 12 12"><path d="M4 2l4 4-4 4" stroke="#fff" stroke-width="2" fill="none"/></svg></div>
  </article>
</section>

<section class="section certs">
  <div class="abs" style="left:141px;top:80px;width:450px">
    <h2 class="heading" style="font-size:29px">Key Industry Certifications</h2>
    <span class="rule rule-left"></span>
    <p class="body-text" style="margin-top:6px">Sed ut perspiciatis unde omnis iste natus error sit voluptatem accusantium doloremque laudantium, totam rem aperiam, eaque ipsa quae ab illo.</p>
    <a class="btn" style="margin-top:16px;height:40px;font-size:11px">Contact Us</a>
  </div>
  <div class="cert-badge" style="left:620px"><span style="background:#d7e6f2"></span></div>
  <div class="cert-badge" style="left:772px"><span style="background:#f3c9cd"></span></div>
  <div class="cert-badge" style="left:924px"><span style="background:#d3d8e8"></span></div>
</section>

<section class="section gallery">
  <div class="abs" style="top:82px;width:100%"><h2 class="heading heading-center">Project Gallery</h2><span class="rule"></span></div>
  <p class="abs body-text" style="top:142px;width:100%;text-align:center">Sed ut perspiciatis unde omnis iste natus error sit voluptatem accusantium doloremque laudantium, totam rem aperiam, eaque ipsa quae ab illo.</p>
  <article class="project" style="left:141px">
    <div class="photo" style="background:linear-gradient(180deg,#2f5fa3 0%,#c9a15a 60%,#7a5a2a 100%)" role="img" aria-label="Building under construction with tower crane at sunrise"></div>
    <h3>Lorem Ipsum Is Simply Dummy Text Of The Printing And Typesetting Industry.</h3>
    <p class="body-text">Sed ut perspiciatis unde omnis iste natus error sit voluptatem accusantium doloremque laudantium, totam rem aperiam, eaque ipsa quae ab illo.</p>
  </article>
  <article class="project" style="left:617px">
    <div class="photo" style="background:linear-gradient(180deg,#9fb6cc 0%,#8a8578 55%,#4a4640 100%)" role="img" aria-label="Classical government building facade with columns"></div>
    <h3>Lorem Ipsum Is Simply Dummy Text Of The Printing And Typesetting Industry.</h3>
    <p class="body-text">Sed ut perspiciatis unde omnis iste natus error sit voluptatem accusantium doloremque laudantium, totam rem aperiam, eaque ipsa quae ab illo.</p>
  </article>
  <a class="btn abs" style="left:512px;top:569px;height:40px;font-size:11px;padding:0 28px">Explore More Projects</a>
</section>

<section class="section why">
  <div class="abs" style="top:80px;width:100%"><h2 class="heading heading-center">Why Choose Us</h2><span class="rule"></span></div>
  <p class="abs body-text" style="top:144px;width:100%;text-align:center">Lorem ipsum dolor sit amet, consectetur adipiscing elit, sed do eiusmod tempor incididunt ut labore et dolore magna aliqua.</p>
  <article class="why-card" style="left:141px"><h3>Veteran-Owned<br>Business</h3><p>Duis aute irure dolor in reprehenderit in voluptate velit esse cillum dolore.</p></article>
  <article class="why-card" style="left:458px"><h3>Experience and<br>Expertise</h3><p>Duis aute irure dolor in reprehenderit in voluptate velit esse cillum dolore.</p></article>
  <article class="why-card" style="left:776px"><h3>Commitment to<br>Quality</h3><p>Duis aute irure dolor in reprehenderit in voluptate velit esse cillum dolore.</p></article>
  <svg class="why-icon" style="left:229px" viewBox="0 0 108 108"><path d="M18 68A40 40 0 0 0 76 88" stroke="#d7141f" stroke-width="2" fill="none"/><circle cx="54" cy="48" r="44" fill="#fff"/><circle cx="54" cy="48" r="38" fill="#14225f"/><path d="M40 66V34h28M46 34v32M40 42h12M62 34v10M58 66h16" stroke="#fff" stroke-width="2.5" fill="none"/></svg>
  <svg class="why-icon" style="left:546px" viewBox="0 0 108 108"><path d="M10 48A44 44 0 0 0 98 48" stroke="#d7141f" stroke-width="2" fill="none"/><circle cx="54" cy="48" r="38" fill="#14225f"/><circle cx="54" cy="40" r="9" stroke="#fff" stroke-width="2.5" fill="none"/><path d="M38 66c2-10 8-14 16-14s14 4 16 14" stroke="#fff" stroke-width="2.5" fill="none"/></svg>
  <svg class="why-icon" style="left:864px" viewBox="0 0 108 108"><path d="M60 4A44 44 0 0 1 98 46" stroke="#d7141f" stroke-width="2" fill="none"/><circle cx="54" cy="48" r="38" fill="#14225f"/><circle cx="54" cy="42" r="12" stroke="#fff" stroke-width="2.5" fill="none"/><path d="M46 52l-6 16 8-3 4 7 2-12M62 52l6 16-8-3-4 7-2-12" stroke="#fff" stroke-width="2" fill="none"/></svg>
</section>

<section class="section reviews">
  <div class="abs" style="top:80px;width:100%"><h2 class="heading heading-center">What Are People Saying?</h2><span class="rule"></span></div>
  <article class="review-card" style="left:141px"><span class="quote"></span><div class="stars">★★★★★</div><p>Lorem ipsum dolor sit amet, consectetur adipiscing elit, sed do eiusmod tempor incididunt ut labore et dolore magna aliqua. Ut enim ad minim veniam, quis nostrud exercitation ullamco laboris nisi.</p><div class="reviewer"><span class="avatar" role="img" aria-label="Reviewer portrait"></span>John Christopher</div></article>
  <article class="review-card" style="left:466px"><span class="quote"></span><div class="stars">★★★★★</div><p>Lorem ipsum dolor sit amet, consectetur adipiscing elit, sed do eiusmod tempor incididunt ut labore et dolore magna aliqua. Ut enim ad minim veniam, quis nostrud exercitation ullamco laboris nisi.</p><div class="reviewer"><span class="avatar" role="img" aria-label="Reviewer portrait"></span>Kate Parker</div></article>
  <article class="review-card" style="left:775px"><span class="quote"></span><div class="stars">★★★★★</div><p>Lorem ipsum dolor sit amet, consectetur adipiscing elit, sed do eiusmod tempor incididunt ut labore et dolore magna aliqua. Ut enim ad minim veniam, quis nostrud exercitation ullamco laboris nisi.</p><div class="reviewer"><span class="avatar" role="img" aria-label="Reviewer portrait"></span>John Christopher</div></article>
  <svg class="abs" style="left:558px;top:444px" width="88" height="34" viewBox="0 0 88 34"><circle cx="17" cy="17" r="15" fill="#fff" stroke="#1a1a1a" stroke-width="1.5"/><path d="M24 17H10m5-5l-5 5 5 5" stroke="#1a1a1a" stroke-width="2" fill="none"/><circle cx="66" cy="17" r="16" fill="#14225f"/><path d="M59 17h14m-5-5l5 5-5 5" stroke="#fff" stroke-width="2" fill="none"/></svg>
</section>

<section class="section cta">
  <div class="abs" style="left:141px;top:160px;width:430px">
    <h2>Lorem Ipsum Dolor Sit Amet, Consectetur Adipiscing Elit</h2>
    <p>Lorem Ipsum is simply dummy text printing and typesetting industry. Lorem Ipsum has been the industry's standard du ever since the 1500s, when an unknown printer took.</p>
    <a class="btn" style="margin-top:22px;height:40px;font-size:11px;padding:0 26px">Project Cosultation</a>
  </div>
  <div class="abs photo" style="left:658px;top:85px;width:401px;height:398px;background:linear-gradient(135deg,#f1f1ef 0%,#d8d8d6 60%,#4a5566 100%)" role="img" aria-label="Businessman on a phone call working at a laptop in an office"></div>
</section>

<footer class="section footer">
  <div class="abs" style="left:141px;top:110px;display:flex;align-items:center;gap:12px;font-family:'Exo 2',sans-serif;font-weight:700;font-size:30px;color:var(--navy)"><span style="width:28px;height:28px;border-radius:50%;background:var(--navy)"></span>TOVANDEX4</div>
  <div class="abs" style="left:459px;top:70px">
    <h4>Quick Links</h4><span class="rule"></span>
    <ul><li>» Home</li><li>» About Us</li><li>» Services</li><li>» Projects</li><li>» Contact Us</li></ul>
  </div>
  <div class="abs" style="left:664px;top:70px;width:190px">
    <h4>Contact Details</h4><span class="rule"></span>
    <div class="contact-item"><svg width="12" height="14" viewBox="0 0 12 14"><path d="M6 0a5 5 0 0 0-5 5c0 4 5 9 5 9s5-5 5-9a5 5 0 0 0-5-5zm0 7a2 2 0 1 1 0-4 2 2 0 0 1 0 4z" fill="#1a1a1a"/></svg><span>123, Building Name, Street<br>City, State XY 123456</span></div>
    <div class="contact-item"><svg width="12" height="12" viewBox="0 0 12 12"><path d="M2 0l3 3-1.5 2a7 7 0 0 0 3.5 3.5L9 7l3 3-2 2C5 12 0 7 0 2z" fill="#1a1a1a"/></svg><span><b>Phone</b><br>123-456-7890</span></div>
    <div class="contact-item"><svg width="13" height="10" viewBox="0 0 13 10"><rect width="13" height="10" rx="1" fill="#1a1a1a"/><path d="M1 1l5.5 4.5L12 1" stroke="#fff" fill="none"/></svg><span><b>Email</b><br>info@tovandex4.com</span></div>
  </div>
  <div class="abs" style="left:969px;top:70px">
    <h4>Follow Us</h4><span class="rule"></span>
    <ul style="margin-top:16px"><li style="margin-bottom:12px"><span class="social-ring"></span>Linkfold</li><li style="margin-bottom:12px"><span class="social-ring"></span>Chirpline</li><li style="margin-bottom:12px"><span class="social-ring"></span>Viewcast</li><li><span class="social-ring"></span>Snapgrid</li></ul>
  </div>
</footer>
<div class="section copyright">© 2024 Tovandex4. All Rights Reserved.</div>

</body>
</html>
```